Systems and Technology Consultants - Website

Design & Build a website for a new company which operates in the Systems and Technology space for Transportation, Government and Commercial sectors.

Overall design should be minimalist in nature.
Should also have a feed that provides news and event updates on the main page.
Logo has already been awarded and should be incorporated into the site.

We like the overall layout, functionality and simplicity of the below sites. Submitted designs could be similar to or a combination of the aspects on these sites, or perhaps a whole different concept - we are open to new ideas.
Norvique.com
Teblo.it

Update 1 Dated 27 May 2014

All I am moving away from the Teblo.it website and would like it to be more aligned with Norvique.com not only in layout but in functionality. I will be extending the deadline of this design brief for two weeks to incorporate additional requirements and will add addtional funding to the project.

Apologies for not having more information available to provide but with so many submissions its getting confusing.

Thanks Derek

Please note that the brief has been updated and the deadline has been extended.

Important: We will need two language versions of the website, English and Arabic; the website is hosted on HostPelican

Hello All, Thank you for your submissions. We have narrowed it down to the final 6 designers and I just wanted to take a moment and provide a bit of feedback regarding the concepts that we like and the modifications we are looking for. First, let me mention some of the design functions we like. - At the top of the homepage we really like the "region" or "language" tab so that the website can be viewed in both English and Arabic. - We like the homepage to have clear color variation so that the different sections of the homepage are distinct. Additionally, we like the bottom portion of the homepage to be in red. We feel that draws attention to our contact information. Again, we would like the colors to integrate black, gray-scale, red, etc. - Having a search tab at the top of the home page, or integrated into the main image, so that the site is easy to navigate. - We especially like the main image to have the scrolling tabs at the bottom so it is easy to browse the services offered (Consultancy, Solutions Architecture, Masters Systems Integration, Independent Design Review). - In regards to the services offered tab we really like the idea that a few people presented that have the outside of our logo with an icon in the middle of consultancy, solutions, etc., etc. Secondly, as mentioned in our brief we really enjoy the design of norvique site. Specially, we enjoy the strong iconic images they use, the way the tabs at the top scroll easily, and contact us page that generates an email. Lastly, I've included some photos of the concept we have been working on. What we are trying to demonstrate is how our company offers a range of services that are essentially linked together. We provide individual services that when combined present the full service package. We would like this concept to be integrated into the over concept of our website. Please feel free to ask for clarification of any of the above points or contact us if you have any additional questions. We appreciate all of your hard work and are very excited to see the updated designs. Best, Marta Vennick Quelbrant Senior Program Manager marta.vennick@quelbrant-example.com

Industry/Entity Type

Government

Font styles to use
Serif
Sans Serif

Requirements
Must have
• Must work on/adapt to various/mobile devices (responsive)
Must be simple and straightforward
Colors should be in line/matching with logo
2 language versions: English and Arabic (no Thai)
Services should be the first group/row of items after/below the main image
Note: the website will be hosted by hostpelican
Nice to have
• Submit feedback form
What's New section
The banner at the bottom of the site should not be too large; we would like a narrow one more
It would be nice if the header/top banner (with Home, About, etc. tabs) could stay in place as you scroll down (like Norvique and Chatterloop)
We will likely only use one image with a Company slogan on the Home page rather than a carousel of images to rotate through
Should not have
• This is the existing website: http://www.quelbrant-example.org
We do not like the animation, the way the banner icons/titles bounce
Not simple enough, we don't like the functionality or how pages load so slowly
We do not like the logo centered - it should be at the left
The banner and its tabs should not be towards the right, we would like them to be centered, to go all the way across and to be below the logo

```html
<!DOCTYPE html>
<html lang="en">
<head>
<meta charset="utf-8">
<title>Quelbrant — Systems and Technology Consultants</title>
<link rel="stylesheet" href="https://fonts.googleapis.com/css2?family=Open+Sans:ital,wght@0,400;0,600;0,700;1,400&display=swap">
<style>
:root{
  --red:#e3191f;
  --ink:#222;
  --body:#555;
  --muted:#8a8a8a;
  --header:#1b1b1b;
  --band:#f1f1f1;
  --footer:#3a3a3a;
  --footer-base:#2b2b2b;
  --footer-text:#a9a9a9;
  --white:#fff;
}
*{box-sizing:border-box;margin:0;padding:0}
html,body{width:771px;height:1200px;overflow:hidden;background:var(--white)}
body{font-family:"Open Sans",Arial,sans-serif;color:var(--ink);position:relative}

/* header */
.site-header{position:absolute;left:0;top:0;width:771px;height:78px;background:linear-gradient(#111,#262626)}
.brand{position:absolute;left:78px;top:24px;display:flex;align-items:center;gap:6px;color:var(--red);font-weight:700;font-size:13px;letter-spacing:1px}
.brand-mark{width:10px;height:10px;background:var(--red)}
.search{position:absolute;left:521px;top:0;width:172px;height:20px;background:var(--white);border-radius:0 0 2px 2px;font-style:italic;font-size:9px;color:#999;padding:4px 7px}
.search svg{position:absolute;right:6px;top:4px}
.main-nav{position:absolute;top:49px;left:0;width:771px;font-size:8.6px;font-weight:600;color:var(--white)}
.main-nav span{position:absolute;white-space:nowrap}
.main-nav .active{border-top:2px solid var(--red);padding-top:4px;margin-top:-6px;padding-left:2px;padding-right:2px}

/* hero */
.hero{position:absolute;left:0;top:78px;width:771px;height:348px;background:linear-gradient(180deg,rgba(255,255,255,0) 55%,rgba(245,245,245,.55) 80%,rgba(120,120,120,.2) 100%),linear-gradient(100deg,#6c6f73 0%,#b9bcbf 35%,#d8d9da 55%,#a7aaad 78%,#5d5f63 100%)}
.hero-caption{position:absolute;left:119px;top:203px;width:546px;height:35px;background:rgba(255,255,255,.88);font-size:12.8px;color:#333;text-align:center;line-height:35px;white-space:nowrap}
.hero-caption b{color:var(--red);font-weight:600}
.hero-caption-2{position:absolute;left:0;width:771px;top:255px;text-align:center;font-size:12.8px;color:#333}

/* vision */
.vision{position:absolute;left:0;top:426px;width:771px;height:204px;background:var(--band);text-align:center}
.vision h2{position:absolute;left:0;width:771px;top:72px;font-weight:400;font-size:16px;color:var(--red)}
.vision .rule{position:absolute;left:320px;top:95px;width:130px;height:1px;background:#d8d8d8}
.vision p{position:absolute;left:110px;width:551px;top:108px;font-size:8.6px;line-height:12.8px;color:var(--body)}
.read-more{position:absolute;left:0;width:771px;top:172px;font-size:8.6px;color:#444;font-weight:600}
.read-more span{text-decoration:underline}

/* services */
.services{position:absolute;left:0;top:630px;width:771px;height:228px;box-shadow:0 6px 8px -6px rgba(0,0,0,.12)}
.service{position:absolute;top:0;width:124px;text-align:center}
.service-icon{position:absolute;left:40px;top:36px;width:44px;height:44px;border:4px solid #2b2b2b;border-radius:50%}
.service-icon i{position:absolute;left:12px;top:12px;width:12px;height:12px;background:var(--red);border-radius:50%}
.service h3{position:absolute;left:0;width:124px;top:104px;font-size:11px;font-weight:600;color:#222}
.service p{position:absolute;left:10px;width:104px;top:130px;font-size:7.4px;line-height:9.2px;color:var(--body)}

/* articles */
.section-title{position:absolute;font-size:14px;font-weight:400;color:var(--red)}
.article-thumb{position:absolute;left:76px;width:52px;height:54px;border:1px solid #ddd;padding:2px;background:var(--white)}
.article-thumb div{width:100%;height:100%}
.article h4{position:absolute;left:136px;font-size:9.6px;font-weight:400;color:#222}
.article p{position:absolute;left:136px;width:280px;font-size:8px;line-height:10.4px;color:var(--muted)}
.article a{position:absolute;left:136px;font-size:8px;color:#222;text-decoration:underline}
.divider{position:absolute;left:445px;top:880px;width:1px;height:184px;background:linear-gradient(#e6e6e6,#fff)}
.news h4{position:absolute;left:454px;font-size:10px;font-weight:400;color:#222}
.news .line{position:absolute;left:454px;font-size:6.6px;color:#222;white-space:nowrap}
.news .date{position:absolute;left:604px;font-size:6.6px;color:var(--red);white-space:nowrap}

/* footer */
.site-footer{position:absolute;left:0;top:1088px;width:771px;height:86px;background:var(--footer)}
.footer-notch{position:absolute;left:378px;top:1088px;width:0;height:0;border-left:6px solid transparent;border-right:6px solid transparent;border-top:6px solid var(--white)}
.footer-links{position:absolute;left:85px;top:1113px;font-size:6.8px;color:var(--footer-text);white-space:nowrap}
.footer-links span{margin:0 5px}
.footer-rule{position:absolute;left:85px;top:1129px;width:448px;height:1px;background:#4d4d4d}
.footer-rule.r{left:546px;width:140px}
.footer-contact{position:absolute;top:1138px;font-size:6.8px;color:var(--footer-text);display:flex;align-items:center;gap:5px;white-space:nowrap}
.stay{position:absolute;left:546px;top:1111px;font-size:6.6px;color:var(--footer-text);letter-spacing:.3px}
.social{position:absolute;top:1137px;width:10px;height:10px;border-radius:50%;background:#6d6d6d}
.base{position:absolute;left:0;top:1174px;width:771px;height:26px;background:var(--footer-base);font-size:7px;color:var(--footer-text)}
.base span{position:absolute;top:9px}
.base .sep{width:1px;height:12px;background:#4a4a4a;top:7px}
</style>
</head>
<body>

<header class="site-header">
  <div class="brand"><span class="brand-mark"></span>QUELBRANT</div>
  <div class="search">Search
    <svg width="12" height="12" viewBox="0 0 12 12"><circle cx="5" cy="5" r="3.8" fill="none" stroke="#e3191f" stroke-width="1.8"/><line x1="7.8" y1="7.8" x2="11" y2="11" stroke="#e3191f" stroke-width="2"/></svg>
  </div>
  <nav class="main-nav">
    <span class="active" style="left:367px">HOME</span>
    <span style="left:412px">Business Units</span>
    <span style="left:488px">Services</span>
    <span style="left:538px">About Us</span>
    <span style="left:593px">Locations</span>
    <span style="left:649px">Contact Us</span>
  </nav>
</header>

<section class="hero" role="img" aria-label="Photo of three colleagues reviewing blueprints on an office table"></section>
<div class="hero-caption"><b>Quelbrant specializes</b> in delivering quality professional services and technical projects</div>
<div class="hero-caption-2">that support larger business goals.</div>

<section class="vision">
  <h2>OUR VISION</h2>
  <div class="rule"></div>
  <p>quelbrant specializes in delivering quality professional services and technical projects that support larger business goals.&nbsp; systems are tools that support a greater business function and need. we understand that most technical projects are conceptualized to support a larger vision with actual business goals in mind and ensure that all of our professional and certified expertise is included in our professional services to meet those goals.</p>
  <div class="read-more"><span>READ MORE</span></div>
</section>

<section class="services">
  <div class="service" style="left:69px"><div class="service-icon" role="img" aria-label="Consulting icon"><i></i></div><h3>Consulting</h3><p>It is a long established fact that a reader will be distracted by the readable content of a page when looking at its layout. The point of using Lorem Ipsum is that it has a more-or-less normal distribution</p></div>
  <div class="service" style="left:204px"><div class="service-icon" role="img" aria-label="Engineering icon"><i></i></div><h3>Engineering</h3><p>It is a long established fact that a reader will be distracted by the readable content of a page when looking at its layout. The point of using Lorem Ipsum is that it has a more-or-less normal distribution</p></div>
  <div class="service" style="left:328px"><div class="service-icon" role="img" aria-label="Construction icon"><i></i></div><h3>Construction</h3><p>It is a long established fact that a reader will be distracted by the readable content of a page when looking at its layout. The point of using Lorem Ipsum is that it has a more-or-less normal distribution</p></div>
  <div class="service" style="left:461px"><div class="service-icon" role="img" aria-label="Operations icon"><i></i></div><h3>Operations</h3><p>It is a long established fact that a reader will be distracted by the readable content of a page when looking at its layout. The point of using Lorem Ipsum is that it has a more-or-less normal distribution</p></div>
  <div class="service" style="left:586px"><div class="service-icon" role="img" aria-label="Maintenance icon"><i></i></div><h3>Maintenance</h3><p>It is a long established fact that a reader will be distracted by the readable content of a page when looking at its layout. The point of using Lorem Ipsum is that it has a more-or-less normal distribution</p></div>
</section>

<h2 class="section-title" style="left:77px;top:880px">Our Articles</h2>
<div class="article">
  <div class="article-thumb" style="top:915px"><div role="img" aria-label="Photo of spiral-bound notebook" style="background:linear-gradient(135deg,#8fa3a6,#d7e0e0,#6e8386)"></div></div>
  <h4 style="top:912px">It is a long established fact that</h4>
  <p style="top:929px">It is a long established fact that a reader will be distracted by the readable content of a page when looking at its layout.</p>
  <a style="top:960px">Read More</a>
</div>
<div class="article">
  <div class="article-thumb" style="top:1002px"><div role="img" aria-label="Photo of a hand writing with a pen" style="background:linear-gradient(135deg,#4c4f55,#c9ccd1,#eef0f2)"></div></div>
  <h4 style="top:999px">It is a long established fact that</h4>
  <p style="top:1016px">It is a long established fact that a reader will be distracted by the readable content of a page when looking at its layout.</p>
  <a style="top:1045px">Read More</a>
</div>

<div class="divider"></div>

<h2 class="section-title" style="left:454px;top:880px">Our News</h2>
<div class="news">
  <h4 style="top:910px">Investing In Real Estate</h4>
  <div class="line" style="top:926px">New terminal opens at Northgate Terminal</div>
  <div class="line" style="top:938px">August 15, 2013 Concessionaire in Kestrel Ridge..</div>
  <div class="line" style="top:950px">Read More...</div>
  <div class="date" style="top:950px">› May 25. February 2014</div>

  <h4 style="top:982px">Current Projects</h4>
  <div class="line" style="top:998px">Concessionaire in Kestrel Ridge..</div>
  <div class="line" style="top:1010px">Resort to Expand Ski Runs at Kestrel Ridge for a Cheap Trip.</div>
  <div class="line" style="top:1022px">Read More...</div>
  <div class="date" style="top:1022px">› May 25. February 2014</div>
</div>

<footer>
  <div class="site-footer"></div>
  <div class="footer-notch"></div>
  <div class="footer-links">Home<span>|</span>About Us<span>|</span>Business Unit<span>|</span>Services<span>|</span>Locations<span>|</span>Contact Us</div>
  <div class="footer-rule"></div>
  <div class="footer-rule r"></div>
  <div class="footer-contact" style="left:85px">
    <svg width="9" height="8" viewBox="0 0 9 8"><path d="M4.5 0L0 4h1.3v4h2.4V5.5h1.6V8h2.4V4H9z" fill="#777"/></svg>
    Lorem Ipsum is simply dummy text of the printinge
  </div>
  <div class="footer-contact" style="left:299px">
    <svg width="8" height="8" viewBox="0 0 8 8"><path d="M1.5 0l1.5 2-1 1c.6 1.3 1.6 2.3 2.9 2.9l1-1L8 6.5 6.8 8C3 7.6.4 5 0 1.2z" fill="#777"/></svg>
    (123) 456-7890
  </div>
  <div class="footer-contact" style="left:383px">
    <svg width="9" height="7" viewBox="0 0 9 7"><rect width="9" height="7" fill="#777"/><path d="M0 0l4.5 3.8L9 0" fill="none" stroke="#3a3a3a" stroke-width="1"/></svg>
    contact@companyname.com
  </div>
  <div class="stay">STAY CONNECTED</div>
  <div class="social" style="left:546px"></div>
  <div class="social" style="left:568px"></div>
  <div class="social" style="left:590px"></div>
  <div class="social" style="left:613px"></div>
  <div class="social" style="left:635px"></div>
  <div class="social" style="left:657px"></div>
  <div class="base">
    <span style="left:81px">Quelbrant © 2014</span>
    <span class="sep" style="left:148px"></span>
    <span style="left:159px">Legal Notice</span>
    <span class="sep" style="left:212px"></span>
    <span style="left:222px">Terms</span>
  </div>
</footer>

</body>
</html>
```